BOLD & MINIMALIST DESIGN NEEDED

We want a very bold but minimalistic business card design that is impactful and utilizes both sides of the business card. Our current logo is included for your use.

We want bold fonts and good use of negative space. We don't want the logo to overpower the design.

Target Market(s)

Professionals who are building new commercial buildings.

Industry/Entity Type

Construction

Contact Information for Business Card

Name, Title, email, office phone, cell phone, website

Font styles to use
Serif
Sans Serif

Requirements
Must have
• Bold design!

```html
<!DOCTYPE html>
<html lang="en">
<head>
<meta charset="utf-8">
<title>Ridgeview Builders – Business Card</title>
<link rel="stylesheet" href="https://fonts.googleapis.com/css2?family=Poppins:wght@400;500;700&display=swap">
<style>
  :root {
    --stage: #2b2b2b;
    --card-dark: #1f1f1f;
    --card-dark-edge: #2c2c2c;
    --card-light: #efefef;
    --ink: #1c1c1c;
    --ink-soft: #333333;
    --white: #ffffff;
    --accent: #7cb82f;
  }
  * { box-sizing: border-box; margin: 0; padding: 0; }
  html, body {
    width: 1200px; height: 576px; overflow: hidden;
    background: var(--stage);
    font-family: "Poppins", sans-serif;
  }
  .canvas { position: relative; width: 1200px; height: 576px; }

  .card {
    position: absolute;
    top: 139px;
    width: 484px; height: 292px;
    border-radius: 9px;
  }
  .card--front {
    left: 102px;
    background: linear-gradient(160deg, var(--card-dark-edge), var(--card-dark));
  }
  .card--back {
    left: 596px;
    width: 480px; height: 290px;
    background: var(--card-light);
  }

  .front-brand {
    position: absolute;
    left: 48px; top: 124px;
    display: flex; align-items: center; gap: 10px;
  }
  .brand-mark {
    width: 14px; height: 14px;
    background: var(--accent);
  }
  .front-brand .brand-name {
    font-weight: 700; font-size: 27px; letter-spacing: 0.5px;
    color: var(--white);
  }

  .back-brand {
    position: absolute;
    left: 54px; top: 130px;
    width: 200px; text-align: center;
    font-weight: 700; font-size: 22px;
    color: var(--ink);
  }

  .contact {
    position: absolute;
    left: 266px; top: 86px;
  }
  .contact .person {
    font-weight: 500; font-size: 19px;
    color: var(--accent); line-height: 1.2;
  }
  .contact .role {
    font-size: 11.5px; color: var(--ink-soft);
    margin-top: 2px;
  }
  .contact-list {
    list-style: none; margin-top: 24px;
  }
  .contact-list li {
    display: flex; align-items: center; gap: 10px;
    font-size: 12px; color: var(--ink-soft);
    height: 17px;
  }
  .contact-list svg { width: 9px; height: 9px; fill: var(--accent); flex: none; }
</style>
</head>
<body>
<div class="canvas">
  <section class="card card--front" aria-label="Card front">
    <div class="front-brand">
      <span class="brand-mark"></span>
      <span class="brand-name">RIDGEVIEW BUILDERS</span>
    </div>
  </section>

  <section class="card card--back" aria-label="Card back">
    <div class="back-brand">RIDGEVIEW BUILDERS</div>

    <div class="contact">
      <p class="person">Daniel Reyes</p>
      <p class="role">Director</p>
      <ul class="contact-list">
        <li>
          <svg viewBox="0 0 10 10" aria-hidden="true"><path d="M1 3 Q1 1 3 1 L7 1 Q9 1 9 3 L9 4 L7 4 L7 3 L3 3 L3 4 L1 4 Z M2 5 L8 5 L9 9 L1 9 Z"/></svg>
          555-014-2270
        </li>
        <li>
          <svg viewBox="0 0 10 10" aria-hidden="true"><path d="M0 2 L10 2 L10 8 L0 8 Z M0.8 2.6 L5 5.6 L9.2 2.6 L9.2 3.4 L5 6.4 L0.8 3.4 Z" fill-rule="evenodd"/></svg>
          daniel@ridgeviewbuild.com
        </li>
        <li>
          <svg viewBox="0 0 10 10" aria-hidden="true"><circle cx="5" cy="5" r="4.5"/></svg>
          www.ridgeviewbuild.com
        </li>
      </ul>
    </div>
  </section>
</div>
</body>
</html>
```